Goat's Milk Soap

International product development company seeking designs for the following soap label:

Hand crafted in Mt Hollowby QLD Australia, Tallow Creek Valley
Second Generation Goat Farmers
Soap is hand made in appearance but gives an instant soothing feel when used
High in Vegetable oils and pure fresh goats milk (no powders used)
Give the emotional feel of Quality and Hand crafted
Label must stimulate an emotional response visually
Label must deliver to the customer anticipation for use.
Would anticipate that the label will be produced on a matte finish brown paper label or similar.

Logo should be no larger than 50mm x 50mm
Label should measure around 120mm x 70mm

It Company

```html
<!DOCTYPE html>
<html lang="en">
<head>
<meta charset="utf-8">
<title>Goat's Milk Soap Label</title>
<link rel="stylesheet" href="https://fonts.googleapis.com/css2?family=Lato:wght@400;700&display=swap">
<style>
  :root {
    --ink: #111111;
    --paper: #ffffff;
    --print-tone: #d9d9d9;
  }
  html, body {
    margin: 0;
    padding: 0;
    width: 1200px;
    height: 1000px;
    overflow: hidden;
    background: var(--paper);
  }
  .canvas {
    position: relative;
    width: 1200px;
    height: 1000px;
    background: var(--paper);
    font-family: "Lato", "Gill Sans", sans-serif;
    color: var(--ink);
  }
  .label-front {
    position: absolute;
    left: 13px;
    top: 35px;
    width: 1173px;
    height: 684px;
    box-sizing: border-box;
    border: 2.5px solid var(--ink);
  }
  .brand-seal {
    position: absolute;
    left: 342px;
    top: 105px;
    width: 498px;
    height: 498px;
    box-sizing: border-box;
    border: 2px solid var(--ink);
    border-radius: 50%;
    display: flex;
    align-items: center;
    justify-content: center;
  }
  .brand-name {
    margin: 0;
    font-family: "Lato", "Gill Sans", sans-serif;
    font-weight: 400;
    font-size: 58px;
    line-height: 1.15;
    text-align: center;
    color: var(--ink);
  }
  .origin-line {
    position: absolute;
    left: 0;
    right: 0;
    top: 616px;
    margin: 0;
    text-align: center;
    font-size: 24.5px;
    letter-spacing: 3.6px;
    text-transform: uppercase;
  }
  .label-back {
    position: absolute;
    left: 13px;
    top: 789px;
    width: 1173px;
    height: 169px;
    box-sizing: border-box;
    border: 2.5px solid var(--ink);
  }
  .hoof-prints {
    position: absolute;
    left: 107px;
    top: 22px;
    width: 166px;
    height: 128px;
    background: var(--print-tone);
  }
  .product-notes {
    position: absolute;
    left: 297px;
    top: 38px;
    margin: 0;
    font-size: 18.5px;
    line-height: 24.5px;
    letter-spacing: 2px;
  }
</style>
</head>
<body>
  <main class="canvas">
    <section class="label-front">
      <div class="brand-seal">
        <h1 class="brand-name">Goat's Milk<br>Soap</h1>
      </div>
      <p class="origin-line">Hand crafted in Mt Hollowby QLD Australia, Tallow Creek Valley</p>
    </section>
    <section class="label-back">
      <div class="hoof-prints" role="img" aria-label="Trail of small goat hoof prints"></div>
      <p class="product-notes">Soap is hand made in appearance but gives an<br>instant soothing feel when used. High in vegetable<br>oils and pure fresh goats milk (no powders used)</p>
    </section>
  </main>
</body>
</html>
```